FinTech company looking to revamp and expand client-facing interface for our financial models

Pellworth Engines currently has a very simple website that allows clients to interact with our financial models. We are looking to completely redesign the current site and add several extra pages to provide extra functionality. We want the design to have a modern, slick feel, that will work on both a desktop or a tablet. It should be straightforward for clients to move between different pages at any time, and clear from the layout how to interact with the more advanced features. We have included screenshots of existing pages in the attached design brief, as well as sketches of the functionality required by the new pages, but can't provide a direct link to the current site.
Target Market(s)
Professional investors that will be paying to access the interface
Industry/Entity Type
Finance
Number of Pages Required
4 page
Colors
Designer to choose colors to be used in the design.
Look and feel
Each slider illustrates characteristics of the customer's brand and the style your logo design should communicate.

```html
<!DOCTYPE html>
<html lang="en">
<head>
<meta charset="utf-8">
<title>VEXA – Models</title>
<link href="https://fonts.googleapis.com/css2?family=Montserrat:wght@500;600;700&family=Roboto+Condensed:wght@400;700&family=Roboto:wght@400;500;700&display=swap" rel="stylesheet">
<style>
  :root{
    --frame:#e6e6e6;
    --white:#ffffff;
    --ink:#111111;
    --dark:#333333;
    --navy:#0b2c5c;
    --grey-head:#626262;
    --row-alt:#f4f4f4;
    --line:#dcdcdc;
    --tab-label:#555555;
    --link:#1f4fa0;
  }
  *{box-sizing:border-box;margin:0;padding:0}
  html,body{width:1200px;height:715px;overflow:hidden;background:var(--frame)}
  body{font-family:"Roboto",Arial,sans-serif;color:var(--ink)}
  .app{position:absolute;left:14px;top:14px;width:1172px;height:687px;
    background:linear-gradient(#cbcbcb 0,#d6d6d6 90px,#f1f1f1 140px,#f7f7f7 500px,#fafafa 100%);}
  .topbar{position:absolute;left:0;top:0;width:1172px;height:55px;background:var(--white);display:flex}
  .brand{width:166px;padding-left:53px;line-height:55px;font:700 17px "Montserrat",sans-serif;letter-spacing:.3px}
  .period{width:83px;text-align:center;line-height:55px;font:700 13px "Montserrat",sans-serif;border-right:1px solid #ececec}
  .period.active{background:var(--dark);color:var(--white);border-right:none}
  .spacer{flex:1}
  .nav{display:flex;align-items:center;justify-content:center;gap:8px;height:55px;font:700 12px "Montserrat",sans-serif;border-left:1px solid #ececec}
  .nav.active{background:var(--dark);color:var(--white);border-left:none}
  .nav svg{width:20px;height:20px}
  .tabs{position:absolute;left:51px;top:92px;display:flex;gap:5px}
  .tab{width:143px;height:51px;background:var(--white);border-radius:5px 5px 0 0;display:flex;flex-direction:column;align-items:center;justify-content:flex-end;padding-bottom:6px;gap:5px;font:500 12px "Roboto Condensed",sans-serif;color:var(--tab-label);letter-spacing:.2px}
  .tab svg{width:18px;height:18px}
  .tab.more{width:38px;justify-content:center;padding:0}
  .filters{position:absolute;left:53px;top:180px;right:0;display:flex;align-items:center;font-size:16px}
  .filters b{font-weight:700;margin:0 12px 0 15px}
  .field{width:166px;height:29px;border:1px solid #cfcfcf;border-radius:3px;background:var(--white);padding:5px 10px;font-size:16px;box-shadow:inset 0 1px 2px rgba(0,0,0,.08)}
  .gap{width:40px}
  .export{position:absolute;right:52px;top:4px;display:flex;align-items:center;gap:8px;color:var(--link);font-weight:700;font-size:16px}
  .grid{position:absolute;left:51px;top:244px;border-collapse:collapse;border-radius:6px;overflow:hidden;box-shadow:0 2px 8px rgba(0,0,0,.12);background:var(--white);table-layout:fixed}
  .grid th{height:65px;color:var(--white);background:var(--grey-head);font:600 15px "Montserrat",sans-serif;text-align:center;border-right:1px solid #777}
  .grid th.key{background:var(--navy);border-right:1px solid #22477c}
  .grid td{height:64px;font:400 15px "Roboto Condensed",sans-serif;padding:0 10px;border-right:1px solid var(--line);border-top:1px solid var(--line);line-height:1.25}
  .grid td.num{text-align:center;padding:0 4px}
  .grid td.id{text-align:center}
  .grid tr:nth-child(even) td{background:var(--row-alt)}
  .grid th:last-child,.grid td:last-child{border-right:none}
</style>
</head>
<body>
<div class="app">
  <header class="topbar">
    <div class="brand">VEXA</div>
    <div class="period active">250D</div>
    <div class="period">83D</div>
    <div class="period">42D</div>
    <div class="spacer"></div>
    <div class="nav active" style="width:130px">
      <svg viewBox="0 0 20 20" fill="none" stroke="currentColor" stroke-width="2"><path d="M2 10 10 3l8 7M5 8v9h4v-5h2v5h4V8"/></svg>MODELS</div>
    <div class="nav" style="width:164px">
      <svg viewBox="0 0 20 20" fill="currentColor"><circle cx="10" cy="10" r="3"/><circle cx="10" cy="3" r="1.5"/><circle cx="10" cy="17" r="1.5"/><circle cx="3" cy="10" r="1.5"/><circle cx="17" cy="10" r="1.5"/><circle cx="5" cy="5" r="1.5"/><circle cx="15" cy="15" r="1.5"/><circle cx="15" cy="5" r="1.5"/><circle cx="5" cy="15" r="1.5"/></svg>SENSITIVITIES</div>
    <div class="nav" style="width:182px">
      <svg viewBox="0 0 20 20" fill="none" stroke="currentColor" stroke-width="1.6"><path d="M10 2l2.4 5.3 5.6.5-4.3 3.8 1.3 5.6L10 14.3 5 17.2l1.3-5.6L2 7.8l5.6-.5z"/></svg>FAVOURITES</div>
  </header>

  <nav class="tabs">
    <div class="tab"><svg viewBox="0 0 18 18" stroke="#555" stroke-width="2"><path d="M2 4h14M2 9h14M2 14h14"/></svg>EQUITIES</div>
    <div class="tab"><svg viewBox="0 0 18 18" fill="#555"><rect x="2" y="10" width="3" height="7"/><rect x="7" y="7" width="3" height="10"/><rect x="12" y="4" width="3" height="13"/></svg>ETFS</div>
    <div class="tab"><svg viewBox="0 0 18 18" fill="none" stroke="#555" stroke-width="1.8"><circle cx="9" cy="9" r="7"/><circle cx="9" cy="9" r="3"/></svg>PAIRS</div>
    <div class="tab"><svg viewBox="0 0 18 18" fill="none" stroke="#555" stroke-width="1.5"><rect x="3" y="1.5" width="12" height="15"/><path d="M6 6h6M6 9h6M6 12h6"/></svg>ETF PAIRS</div>
    <div class="tab"><svg viewBox="0 0 18 18" fill="#555"><path d="M6 3l6-2v14l-6 2z"/></svg>FACTORS</div>
    <div class="tab"><svg viewBox="0 0 18 18" stroke="#999" stroke-width="1.5"><path d="M3 3l12 12M15 3 3 15M9 2v14M2 9h14"/></svg>NEW TAB TITLE #1</div>
    <div class="tab"><svg viewBox="0 0 18 18" fill="none" stroke="#555" stroke-width="1.5"><rect x="1" y="9" width="4" height="6" rx="2"/><rect x="7" y="6" width="4" height="6" rx="2"/><rect x="13" y="3" width="4" height="6" rx="2"/></svg>NEW TAB TITLE #2</div>
    <div class="tab more"><svg viewBox="0 0 18 18" fill="none" stroke="#aaa" stroke-width="2.5"><path d="M6 3l6 6-6 6"/></svg></div>
  </nav>

  <section class="filters">
    <span>Quality</span><b>Threshold:</b><div class="field">-10</div>
    <div class="gap"></div>
    <span><b style="margin:0">Abs.</b> Stat</span><b>Threshold:</b><div class="field">-10</div>
    <div class="export"><svg width="24" height="20" viewBox="0 0 24 20" fill="none" stroke="currentColor" stroke-width="2"><path d="M10 3H4v15h15v-6M13 2h8v8M21 2l-9 9"/></svg>Export</div>
  </section>

  <table class="grid">
    <colgroup><col style="width:93px"><col style="width:102px"><col style="width:106px"><col style="width:106px"><col span="8" style="width:83px"></colgroup>
    <thead><tr><th class="key">ID &#8964;</th><th class="key">Sector</th><th class="key">Time</th><th>Quality</th><th>Stat 1</th><th>Stat 2</th><th>Stat 3</th><th>Stat 4</th><th>Stat 5</th><th>Stat 6</th><th>Stat 7</th><th>Stat 8</th></tr></thead>
    <tbody>
      <tr><td class="id">Model 1</td><td>Materials</td><td class="num">2019-07-03<br>12:15:00.000</td><td class="num">30.2288</td><td class="num">2.01574</td><td class="num">23.305</td><td class="num">-0.149368</td><td class="num">22.3054</td><td class="num">4.63714</td><td class="num">0.945706</td><td class="num">2.81949</td><td class="num">2.60858</td></tr>
      <tr><td class="id">Model 2</td><td>Industrials</td><td class="num">2019-07-03<br>12:15:00.000</td><td class="num">32.8694</td><td class="num">0.87307</td><td class="num">32.185</td><td class="num">-0.033692</td><td class="num">33.9911</td><td class="num">11.5693</td><td class="num">-0.472968</td><td class="num">-0.830458</td><td class="num">6.80646</td></tr>
      <tr><td class="id">Model 3</td><td>Consumer Discretionary</td><td class="num">2019-07-03<br>12:15:00.000</td><td class="num">1.66002</td><td class="num">-0.569222</td><td class="num">159.814</td><td class="num">0.0252328</td><td class="num">172.616</td><td class="num">10.2875</td><td class="num">-0.750396</td><td class="num">-0.385309</td><td class="num">4.69146</td></tr>
      <tr><td class="id">Model 4</td><td>Information Technology</td><td class="num">2019-07-03<br>12:15:00.000</td><td class="num">45.6856</td><td class="num">0.412148</td><td class="num">202.488</td><td class="num">0.0084923</td><td class="num">205.834</td><td class="num">11.9094</td><td class="num">-0.137913</td><td class="num">0.449595</td><td class="num">3.85106</td></tr>
      <tr><td class="id">Model 5</td><td>Information Technology</td><td class="num">2019-07-03<br>12:15:00.000</td><td class="num">75.7733</td><td class="num">7.06728</td><td class="num">188.605</td><td class="num">0.016913</td><td class="num">161.665</td><td class="num">3.82241</td><td class="num">0.981019</td><td class="num">1.29847</td><td class="num">3.34927</td></tr>
    </tbody>
  </table>
</div>
</body>
</html>
```